sydney wedding photography business needs a business card design

we need a business card design for a sydney based wedding photography and videography business. our business name is :golden hour studio and film. our target clients are 24-35 yrs female. our style is candid, organic, natural, dynamic. we are a team of young photographers and videographers, and help brides to create memories that they will cherish for the rest of their lives. the logo will be provided. we want an elegant design that reflects our style, and also want to give a great impression to our clients that we are one of the best studios in sydney and our brand means quality and premium service.

Target Market(s)

bride to be, 24-35 years old, living in sydney and surrunding areas

Industry/Entity Type

Wedding Photography

Contact Information for Business Card

address: 57 tarrant street, glenmore nsw 2047
mobile: 0431872259
phone: (02) 9163 2408
info@tidewillowstudio.net.au
www.tidewillowstudio.net.au
facebook:tidewillowweddings
instagram:tidewillowweddings

Font styles to use
Serif
Sans Serif

Requirements
Nice to have
• maybe add my slogan"memories beyond eternity" if the layout looks good
Should not have
• no black color, not good idea for wedding biz card

```html
<!DOCTYPE html>
<html lang="en">
<head>
<meta charset="utf-8">
<title>Golden Hour Studio and Film – Business Card</title>
<link rel="stylesheet" href="https://fonts.googleapis.com/css2?family=Didact+Gothic&display=swap">
<style>
  :root {
    --backdrop: #e9e4dc;
    --paper: #ffffff;
    --ink: #3a3129;
    --gold: #c9961f;
    --gold-deep: #a87812;
    --gold-light: #e0b340;
    --cocoa-top: #5a4631;
    --cocoa-bottom: #3b2d1f;
    --glow: #7a6244;
    --shadow: rgba(60, 45, 25, 0.26);
  }
  * { margin: 0; padding: 0; box-sizing: border-box; }
  html, body {
    width: 1200px;
    height: 950px;
    overflow: hidden;
    background: var(--backdrop);
    font-family: "Didact Gothic", "Century Gothic", sans-serif;
  }
  .sheet {
    position: relative;
    width: 1200px;
    height: 950px;
  }
  .card {
    position: absolute;
    left: 280px;
    width: 640px;
    height: 390px;
    border-radius: 3px;
    overflow: hidden;
    box-shadow: 0 14px 30px var(--shadow);
  }
  .card--front { top: 60px; background: var(--paper); }
  .card--back {
    top: 500px;
    background: linear-gradient(135deg, var(--gold-light) 0%, var(--gold) 45%, var(--gold-deep) 100%);
  }

  /* front: white information panel */
  .info {
    position: absolute;
    left: 0; top: 0;
    width: 100%;
    height: 232px;
    padding: 22px 0 0 300px;
    color: var(--ink);
  }
  .info__name {
    color: var(--gold);
    font-size: 23px;
    font-weight: 400;
    letter-spacing: 1px;
    text-transform: uppercase;
    line-height: 1.1;
  }
  .info__role {
    font-size: 14px;
    text-transform: uppercase;
    letter-spacing: 0.5px;
    margin-top: 2px;
  }
  .info__address {
    font-size: 13px;
    line-height: 16px;
    margin-top: 12px;
  }
  .contacts {
    list-style: none;
    margin-top: 10px;
    font-size: 13px;
    line-height: 17px;
  }
  .contacts li {
    display: flex;
    align-items: center;
    gap: 9px;
  }
  .contacts .icon {
    width: 10px;
    height: 10px;
    flex: none;
  }
  .contacts .icon--square { background: var(--gold); border-radius: 2px; }

  .divider {
    position: absolute;
    left: 0; top: 232px;
    width: 100%;
    height: 4px;
    background: var(--gold);
  }

  /* front: deep cocoa brand panel */
  .brand {
    position: absolute;
    left: 0; top: 236px;
    width: 100%;
    height: 154px;
    overflow: hidden;
    background: linear-gradient(160deg, var(--cocoa-top) 0%, var(--cocoa-bottom) 100%);
  }
  .brand__decoration {
    position: absolute;
    left: 40px;
    top: 0;
    width: 230px;
    height: 150px;
  }
  .brand__name {
    position: absolute;
    left: 40px;
    bottom: 34px;
    color: var(--gold-light);
    font-size: 25px;
    font-weight: 400;
    letter-spacing: 0.5px;
  }
</style>
</head>
<body>
  <main class="sheet">
    <section class="card card--front" aria-label="Business card front">
      <div class="info">
        <h1 class="info__name">Lena Hartwell</h1>
        <p class="info__role">Photographer</p>
        <p class="info__address">57 tarrant street<br>glenmore nsw 2047</p>
        <ul class="contacts">
          <li>
            <svg class="icon" viewBox="0 0 10 10" aria-hidden="true">
              <path d="M2 0.6 L3.6 2.8 L2.7 3.8 C3.3 5.2 4.6 6.6 6.1 7.3 L7.1 6.4 L9.4 8 L8.3 9.5 C4.3 9.2 0.8 5.8 0.5 1.7 Z" fill="var(--gold)"/>
            </svg>
            <span>(02) 9163 2408</span>
          </li>
          <li><span class="icon icon--square"></span><span>0431 872 259</span></li>
          <li><span class="icon icon--square"></span><span>info@tidewillowstudio.net.au</span></li>
          <li>
            <svg class="icon" viewBox="0 0 10 10" aria-hidden="true">
              <circle cx="5" cy="5" r="4.6" fill="var(--gold)"/>
            </svg>
            <span>www.tidewillowstudio.net.au</span>
          </li>
          <li><span class="icon icon--square"></span><span>tidewillowweddings</span></li>
          <li><span class="icon icon--square"></span><span>tidewillowweddings</span></li>
        </ul>
      </div>
      <div class="divider"></div>
      <div class="brand">
        <svg class="brand__decoration" role="img" aria-label="Faint ring illustration behind the studio name" viewBox="0 0 230 150">
          <defs>
            <radialGradient id="ringGlow" cx="50%" cy="40%" r="60%">
              <stop offset="0%" stop-color="var(--glow)" stop-opacity="0.55"/>
              <stop offset="100%" stop-color="var(--glow)" stop-opacity="0"/>
            </radialGradient>
          </defs>
          <rect width="230" height="150" fill="url(#ringGlow)"/>
        </svg>
        <p class="brand__name">golden hour studio and film</p>
      </div>
    </section>

    <section class="card card--back" aria-label="Business card back"></section>
  </main>
</body>
</html>
```